VFX Company Business Card Design Project

The Kestrel Works is a decentralized Visual Effects Studio servicing the television and feature film industries.
Project Brief:
Take our logo that was previously designed on Pencil Harbor and make a double sided business card.
Requirements:
- Card MUST be double sided.
- Front of card MUST have the yellow part of our logo against the dark grey background.
- Back of card is completely up to the designer.
- Back of card must include the complete company logo.
Please follow these File Preparation guidelines:
http://printnook.ca/infopage?file=filetype_en&s=PrintNook_new&lang=en
Business

```html
<!DOCTYPE html>
<html lang="en">
<head>
<meta charset="utf-8">
<title>The Kestrel Works – Business Cards</title>
<link rel="stylesheet" href="https://fonts.googleapis.com/css2?family=Montserrat:wght@400;600&family=Quicksand:wght@500&display=swap">
<style>
  :root {
    --stage: #8a5532;
    --card: #262626;
    --brand-yellow: #fcc62a;
    --ink-light: #edf1e6;
    --ink-grey: #5f6b6c;
    --band: #e9efe2;
    --band-ink: #2a2a2a;
  }
  * { margin: 0; padding: 0; box-sizing: border-box; }
  html, body { width: 1200px; height: 727px; overflow: hidden; }
  body {
    position: relative;
    background: var(--stage);
    font-family: "Montserrat", sans-serif;
  }
  .card {
    position: absolute;
    width: 525px;
    height: 300px;
    background: var(--card);
    border-radius: 28px;
    overflow: hidden;
  }
  .card--front { left: 68px; top: 42px; }
  .card--contact { left: 628px; top: 47px; }
  .card--lockup { left: 65px; top: 383px; }
  .card--wordmark { left: 623px; top: 388px; }

  .brand-name {
    font-family: "Montserrat", sans-serif;
    font-weight: 600;
    text-transform: uppercase;
    white-space: nowrap;
    line-height: 1;
  }
  .tagline {
    font-family: "Montserrat", sans-serif;
    font-weight: 400;
    text-transform: uppercase;
    color: var(--ink-light);
    white-space: nowrap;
  }
  .web {
    position: absolute;
    left: 0; right: 0;
    text-align: center;
    font-family: "Quicksand", sans-serif;
    font-weight: 500;
    font-size: 18px;
    letter-spacing: 2.4px;
    color: var(--ink-light);
  }

  /* Front */
  .card--front .front-mark {
    position: absolute;
    left: 0; right: 0; top: 118px;
    display: flex; align-items: center; justify-content: center; gap: 18px;
  }
  .front-mark .dot {
    width: 44px; height: 44px; border-radius: 50%;
    background: var(--brand-yellow);
  }
  .front-mark .brand-name { color: var(--brand-yellow); font-size: 34px; }

  /* Contact */
  .card--contact .brand-name { position: absolute; left: 44px; top: 62px; font-size: 34px; color: var(--ink-light); }
  .card--contact .tagline { position: absolute; left: 86px; top: 104px; font-size: 16px; letter-spacing: 7.5px; }
  .contact-list {
    position: absolute; left: 42px; top: 163px;
    list-style: none;
    font-family: "Quicksand", sans-serif; font-size: 14px; color: var(--ink-light);
  }
  .contact-list li { display: flex; align-items: center; gap: 6px; height: 21px; }
  .contact-list svg { width: 12px; height: 12px; fill: var(--ink-light); }
  .person { position: absolute; right: 58px; top: 181px; text-align: right; color: var(--ink-light); }
  .person-name { font-family: "Quicksand", sans-serif; font-size: 20px; }
  .person-title { font-family: "Quicksand", sans-serif; font-size: 13px; margin-top: 2px; }
  .address-band {
    position: absolute; left: 0; right: 0; bottom: 0; height: 31px;
    background: var(--band);
    display: flex; align-items: center; gap: 7px; padding-left: 42px;
    font-family: "Quicksand", sans-serif; font-size: 14px; color: var(--band-ink);
  }
  .address-band svg { width: 12px; height: 12px; fill: var(--band-ink); }

  /* Lockup */
  .card--lockup .lockup {
    position: absolute; left: 38px; top: 112px;
    display: flex; align-items: center; gap: 16px;
  }
  .lockup .dot { width: 40px; height: 40px; border-radius: 50%; background: var(--brand-yellow); }
  .lockup .brand-name { font-size: 30px; color: var(--ink-light); }
  .card--lockup .tagline { position: absolute; left: 96px; top: 158px; font-size: 14px; letter-spacing: 7px; }
  .card--lockup .web { top: 256px; }

  /* Wordmark */
  .card--wordmark .brand-name { position: absolute; left: 0; right: 0; top: 108px; text-align: center; font-size: 40px; color: var(--ink-light); }
  .card--wordmark .tagline { position: absolute; left: 0; right: 0; top: 162px; text-align: center; font-size: 20px; letter-spacing: 9px; }
  .card--wordmark .web { top: 256px; }
</style>
</head>
<body>

<section class="card card--front" aria-label="Card front">
  <div class="front-mark">
    <span class="dot"></span>
    <span class="brand-name">The Kestrel Works</span>
  </div>
</section>

<section class="card card--contact" aria-label="Card back with contact details">
  <div class="brand-name">The Kestrel Works</div>
  <div class="tagline">Virtual Studio</div>
  <ul class="contact-list">
    <li><svg viewBox="0 0 12 12"><path d="M2.5 1l2 2-1 1.5c.7 1.5 1.8 2.6 3.3 3.3L8.3 6.8l2 2-1.3 2C5 10.5 1.5 7 1 2.5z"/></svg>0987 654321</li>
    <li><svg viewBox="0 0 12 12"><rect x="3" y="0.5" width="6" height="11" rx="1.2"/><rect x="4" y="2" width="4" height="6.5" fill="#262626"/></svg>0987 654321</li>
    <li><svg viewBox="0 0 12 12"><path d="M1 3h10v7H1z"/><path d="M1 3l5 4 5-4" fill="none" stroke="#262626" stroke-width="1"/></svg>info@kestrelworks.com</li>
    <li><svg viewBox="0 0 12 12"><circle cx="6" cy="6" r="5" fill="none" stroke="#edf1e6" stroke-width="1"/><ellipse cx="6" cy="6" rx="2.2" ry="5" fill="none" stroke="#edf1e6" stroke-width="1"/><path d="M1 6h10" stroke="#edf1e6" stroke-width="1"/></svg>www.kestrelworks.com</li>
  </ul>
  <div class="person">
    <div class="person-name">Your Name</div>
    <div class="person-title">Title</div>
  </div>
  <div class="address-band">
    <svg viewBox="0 0 12 12"><path d="M6 0.5a4 4 0 0 1 4 4c0 3-4 7-4 7s-4-4-4-7a4 4 0 0 1 4-4z"/><circle cx="6" cy="4.5" r="1.5" fill="#e9efe2"/></svg>
    00, Complex name, City, State 0042
  </div>
</section>

<section class="card card--lockup" aria-label="Card back with full logo">
  <div class="lockup">
    <span class="dot"></span>
    <span class="brand-name">The Kestrel Works</span>
  </div>
  <div class="tagline">Virtual Studio</div>
  <div class="web">www.kestrelworks.com</div>
</section>

<section class="card card--wordmark" aria-label="Card back with wordmark">
  <div class="brand-name">The Kestrel Works</div>
  <div class="tagline">Virtual Studio</div>
  <div class="web">www.kestrelworks.com</div>
</section>

</body>
</html>
```